Property Maintenance company needs a noticeable Car Wrap design

We need an outstanding car wrap design for our Harlow Bex Travanta Metro 2020. It needs to emphasize that our property maintenance company serves both Commercial and Residential clients. The wrap should communicate friendliness and quality services. I have attached a pdf file that outlines all the requirements for the wrap design. I also attached all relevant pictures to help with the creation of the design. The selected winner will receive the source files of the company logo & QNT logo to use in the car wrap design. I look forward to seeing all your designs!

Thank you!
Updates

Need extra days to review

Target Market(s)

Property Maintenance
Residential homeowners
Building owners

Industry/Entity Type

Property Maintenance

Requirements
Must have
• See Instruction file for all details.
Nice to have
• Some small icons that represent electrical, plumbing, handyman, and carpentry work.
For example, like a lightbulb, plug, or pipe icon. Or all of them. Try to use intuitive icons so the general public will know what it is.

Thanks!

```html
<!DOCTYPE html>
<html lang="en">
<head>
<meta charset="utf-8">
<title>TrueReach Maintenance Services – Vehicle Wrap Sides</title>
<link href="https://fonts.googleapis.com/css2?family=Montserrat:wght@400;500;600;700&family=Oswald:wght@700&display=swap" rel="stylesheet">
<style>
  :root {
    --wrap-blue: #2b3990;
    --wrap-green: #6cbf45;
    --wrap-white: #f4f5f6;
    --panel-edge: #d5d8dc;
    --page-bg: #ffffff;
  }
  html, body {
    margin: 0;
    padding: 0;
    width: 1200px;
    height: 1132px;
    overflow: hidden;
    background: var(--page-bg);
  }
  .canvas {
    position: relative;
    width: 1200px;
    height: 1132px;
  }
  .wrap-side {
    position: absolute;
    left: 50px;
    width: 1100px;
    height: 440px;
  }
  .wrap-side--driver { top: 90px; }
  .wrap-side--passenger { top: 602px; }
  .panel-base { fill: var(--wrap-white); stroke: var(--panel-edge); stroke-width: 2; }
  .band-blue { fill: var(--wrap-blue); }
  .band-green { fill: var(--wrap-green); }
  .brand-name {
    font-family: 'Montserrat', sans-serif;
    font-weight: 700;
    font-size: 40px;
    fill: var(--wrap-blue);
    letter-spacing: 1px;
  }
  .brand-mark { fill: var(--wrap-green); }
  .brand-tagline {
    font-family: 'Montserrat', sans-serif;
    font-weight: 600;
    font-size: 12px;
    letter-spacing: 6.5px;
    fill: var(--wrap-blue);
  }
  .phone {
    font-family: 'Oswald', sans-serif;
    font-weight: 700;
    font-size: 56px;
    fill: var(--wrap-blue);
  }
  .web-address {
    font-family: 'Montserrat', sans-serif;
    font-weight: 500;
    font-size: 27px;
    letter-spacing: 5px;
    fill: var(--wrap-white);
  }
  .service {
    font-family: 'Montserrat', sans-serif;
    font-weight: 600;
    font-size: 17px;
    fill: var(--wrap-white);
  }
  .service-dot { fill: var(--wrap-white); }
</style>
</head>
<body>
<main class="canvas">

  <!-- Driver side: cab on the left, rear on the right -->
  <svg class="wrap-side wrap-side--driver" viewBox="0 0 1100 440" aria-label="Driver side wrap">
    <defs>
      <clipPath id="panel-clip-a"><rect x="0" y="0" width="1100" height="440" rx="28"/></clipPath>
    </defs>
    <rect class="panel-base" x="1" y="1" width="1098" height="438" rx="28"/>
    <g clip-path="url(#panel-clip-a)">
      <path class="band-green" d="M0,282 L760,192 Q850,180 880,132 L962,0 L1015,0 L915,170 Q880,232 770,246 L0,336 Z"/>
      <path class="band-blue" d="M0,346 L775,256 Q900,240 940,176 L1040,0 L1100,0 L1100,440 L0,440 Z"/>
    </g>

    <g class="brand-lockup">
      <rect class="brand-mark" x="430" y="54" width="14" height="14"/>
      <text class="brand-name" x="452" y="70">TRUEREACH</text>
      <text class="brand-tagline" x="432" y="100">MAINTENANCE SERVICES</text>
    </g>
    <text class="phone" x="430" y="168">403-555-0148</text>

    <text class="web-address" transform="translate(300 290) rotate(-6.76)">www.truereachpm.com</text>

    <g class="services">
      <circle class="service-dot" cx="132" cy="384" r="5"/>
      <text class="service" x="146" y="390">GENERAL MAINTENANCE/</text>
      <text class="service" x="146" y="414">HANDYMAN REPAIRS</text>
      <circle class="service-dot" cx="532" cy="384" r="5"/>
      <text class="service" x="546" y="390">COMMERCIAL &amp; RESIDENTIAL</text>
      <text class="service" x="546" y="414">RENOVATIONS</text>
    </g>
  </svg>

  <!-- Passenger side: rear on the left, cab on the right -->
  <svg class="wrap-side wrap-side--passenger" viewBox="0 0 1100 440" aria-label="Passenger side wrap">
    <defs>
      <clipPath id="panel-clip-b"><rect x="0" y="0" width="1100" height="440" rx="28"/></clipPath>
    </defs>
    <rect class="panel-base" x="1" y="1" width="1098" height="438" rx="28"/>
    <g clip-path="url(#panel-clip-b)">
      <g transform="translate(1100 0) scale(-1 1)">
        <path class="band-green" d="M0,282 L760,192 Q850,180 880,132 L962,0 L1015,0 L915,170 Q880,232 770,246 L0,336 Z"/>
        <path class="band-blue" d="M0,346 L775,256 Q900,240 940,176 L1040,0 L1100,0 L1100,440 L0,440 Z"/>
      </g>
    </g>

    <g class="brand-lockup">
      <rect class="brand-mark" x="370" y="54" width="14" height="14"/>
      <text class="brand-name" x="392" y="70">TRUEREACH</text>
      <text class="brand-tagline" x="372" y="100">MAINTENANCE SERVICES</text>
    </g>
    <text class="phone" x="370" y="168">403-555-0148</text>

    <text class="web-address" transform="translate(420 246) rotate(6.76)">www.truereachpm.com</text>

    <g class="services">
      <circle class="service-dot" cx="142" cy="384" r="5"/>
      <text class="service" x="156" y="390">GENERAL MAINTENANCE/</text>
      <text class="service" x="156" y="414">HANDYMAN REPAIRS</text>
      <circle class="service-dot" cx="542" cy="384" r="5"/>
      <text class="service" x="556" y="390">COMMERCIAL &amp; RESIDENTIAL</text>
      <text class="service" x="556" y="414">RENOVATIONS</text>
    </g>
  </svg>

</main>
</body>
</html>
```